Dovecote Realty

Business cards for 4 people

They need to say for all
87 Tarrow Quay, Boston MA 02114

Each person will have their own personal information
We would like gold embossing for the name of the company
Marla is the blonde sitting in the chair smiling her information should be on the back of the card with her name and information
Should say for slogan classic pattern, elevated experience
grace@dovecoteprops.com
(413) 555-0182

Odette is the brunette with wavy hair in the tan suit odette@dovecoteprops.com
(617) 555-0137

faith@dovecoteprops.com
(413) 555-0164
standing next to the chair

hope@dovecoteprops.com
(413) 555-0199
close up headshot

```html
<!DOCTYPE html>
<html lang="en">
<head>
<meta charset="utf-8">
<title>Dovecote Realty – Business Cards</title>
<link rel="stylesheet" href="https://fonts.googleapis.com/css2?family=Open+Sans:wght@400;600;700&display=swap">
<style>
  :root {
    --stage: #1d1d20;
    --gold: #ebb969;
    --gold-deep: #d9a24a;
    --gold-text: #e8b35f;
    --card-dark: #2a2a2e;
    --ink-light: #f1f1f1;
    --photo-a: #4a3a2e;
    --photo-b: #8a6544;
  }
  * { box-sizing: border-box; margin: 0; padding: 0; }
  html, body { width: 1200px; height: 780px; overflow: hidden; }
  body {
    background: var(--stage);
    font-family: "Open Sans", sans-serif;
    display: flex;
    align-items: center;
    justify-content: center;
    gap: 40px;
  }
  .card {
    width: 560px;
    height: 320px;
    position: relative;
    overflow: hidden;
  }

  /* Front */
  .card-front {
    background: var(--gold);
    display: flex;
    align-items: center;
    justify-content: center;
  }
  .brand {
    display: flex;
    align-items: center;
    gap: 16px;
  }
  .brand-circle {
    border-radius: 50%;
    border: 3px solid var(--gold-deep);
    flex: none;
  }
  .card-front .brand-circle { width: 64px; height: 64px; }
  .brand-name {
    font-family: "Open Sans", sans-serif;
    font-weight: 600;
    letter-spacing: 0.08em;
    text-transform: uppercase;
    white-space: nowrap;
  }
  .card-front .brand-name { color: var(--gold-deep); font-size: 34px; }

  /* Back */
  .card-back {
    background: var(--card-dark);
    border-left: 2px solid var(--gold);
    border-bottom: 2px solid var(--gold);
  }
  .name-tab {
    position: absolute;
    top: 0;
    right: 0;
    width: 22px;
    height: 46px;
    background: var(--gold);
  }
  .person {
    position: absolute;
    top: 16px;
    right: 34px;
    text-align: right;
  }
  .person-name {
    color: var(--gold-text);
    font-weight: 700;
    font-size: 25px;
    line-height: 1.1;
  }
  .person-title {
    color: var(--ink-light);
    font-size: 10.5px;
    font-weight: 600;
    margin-top: 3px;
  }
  .portrait {
    position: absolute;
    right: 0;
    bottom: 0;
    width: 210px;
    height: 230px;
    background: linear-gradient(160deg, var(--photo-b), var(--photo-a));
    border-radius: 90px 90px 0 0;
  }
  .card-back .brand {
    position: absolute;
    left: 30px;
    top: 92px;
    gap: 10px;
  }
  .card-back .brand-circle { width: 40px; height: 40px; border-color: var(--gold-text); border-width: 2px; }
  .card-back .brand-name { color: var(--gold-text); font-size: 19px; }
  .contact {
    position: absolute;
    left: 30px;
    bottom: 22px;
    color: var(--ink-light);
    font-size: 14px;
    line-height: 1.4;
  }
  .address { margin-bottom: 8px; }
  .contact-line {
    display: flex;
    align-items: center;
    gap: 8px;
  }
  .contact-line svg { width: 13px; height: 13px; flex: none; }
</style>
</head>
<body>

  <section class="card card-front">
    <div class="brand">
      <span class="brand-circle"></span>
      <span class="brand-name">Dovecote Realty</span>
    </div>
  </section>

  <section class="card card-back">
    <span class="name-tab"></span>
    <div class="person">
      <p class="person-name">Odette Lavallee</p>
      <p class="person-title">Real Estate Advisor and Sales Manager</p>
    </div>

    <div class="portrait" role="img" aria-label="Portrait photo of Odette, brunette with wavy hair in a tan suit"></div>

    <div class="brand">
      <span class="brand-circle"></span>
      <span class="brand-name">Dovecote Realty</span>
    </div>

    <div class="contact">
      <p class="address">87 Tarrow Quay,<br>Boston MA 02114</p>
      <p class="contact-line">
        <svg viewBox="0 0 24 24" aria-hidden="true"><path fill="#e8b35f" d="M6.6 10.8a15.1 15.1 0 0 0 6.6 6.6l2.2-2.2a1 1 0 0 1 1-.25 11.4 11.4 0 0 0 3.6.57 1 1 0 0 1 1 1V20a1 1 0 0 1-1 1A17 17 0 0 1 3 4a1 1 0 0 1 1-1h3.5a1 1 0 0 1 1 1c0 1.25.2 2.450.57 3.57a1 1 0 0 1-.25 1z"/></svg>
        (617) 555-0137
      </p>
      <p class="contact-line">
        <svg viewBox="0 0 24 24" aria-hidden="true"><circle cx="12" cy="12" r="9" fill="none" stroke="#e8b35f" stroke-width="2"/><path d="M3 12h18M12 3c3 3 3 15 0 18M12 3c-3 3-3 15 0 18" fill="none" stroke="#e8b35f" stroke-width="1.6"/></svg>
        www.dovecoteprops.com
      </p>
      <p class="contact-line">
        <svg viewBox="0 0 24 24" aria-hidden="true"><rect x="2" y="5" width="20" height="14" rx="1.5" fill="none" stroke="#e8b35f" stroke-width="2"/><path d="M3 6l9 7 9-7" fill="none" stroke="#e8b35f" stroke-width="2"/></svg>
        odette@dovecoteprops.com
      </p>
    </div>
  </section>

</body>
</html>
```